Online Advertising: What gets us excited?

We need a poster that helps make it obvious who we are as a software delivery team.

Background: Our company's culture thrives on "ideas". We use those ideas from every member of our team to innovate and beat out the competition. We hire the kind of people that are bursting with ideas and just need a place to put them into practice.

Design Brief: In this poster design, I imagine a cross between those standard "inspirational posters", like http://qvx.example/t7mWpa

a funny cartoon, like a Odd Porch comic http://qvx.example/k4hNbd

and an TJ Rolwand morphing of shapes. http://qvx.example/w2yPuf

The picture should embody this: A computer programmer wrapped in ideas as an artist painting systems onto a canvas. The canvas sits on an easel that represents our suite of web advertising products. And the artist works amongst others in the Brindle Works art studio, which represents our company headquarters.

The tagline might read:
"Brindle Works products are the canvas where I paint my ideas!"

I am not disclosing the name of the company, so feel free to use "Brindle Works". Feel free to ask any questions you like.

For the winning design, I will likely followup with additional adjustments and variations on this theme.

Reason: 5 days was not enough time for all of us. I did not provide feedback quickly enough for you to hone your designs. Please do continue to develop your ideas a bit, based on my feedback.

Reason: Allow for more designs. None of the images are exactly hitting that right sense of creativity and software creation, being combined.

Target Market(s)

Our employees, especially our engineering team of programmers, testers, web designers, project managers, and product managers.

Industry/Entity Type

Software

Font styles to use
Sans Serif

Requirements
Must have
• Immediate appeal. Easy to understand at a glance, yet nuanced deeper meaning.
Nice to have
• Fine details that intrigue people.
Should not have
• Gender bias - must support men and women. Racial bias - must not exclude any races.

```html
<!DOCTYPE html>
<html lang="en">
<head>
<meta charset="utf-8">
<title>Brindle Works products – The Canvas</title>
<link rel="stylesheet" href="https://fonts.googleapis.com/css2?family=Cutive+Mono&family=Special+Elite&family=Dancing+Script:wght@700&display=swap">
<style>
  :root {
    --paper: #ffffff;
    --stroke-blue: #a9d6ec;
    --stroke-violet: #8f7fc4;
    --stroke-green: #9fd39a;
    --stroke-pink: #f2b8c8;
    --photo-green: #2f9a3c;
    --photo-olive: #8aa62a;
    --photo-orange: #e8541c;
    --photo-red: #d8261a;
    --photo-dark: #2a0706;
    --title-teal: #7ecaca;
    --title-edge: #2f5d5f;
    --ink: #1a1414;
    --tagline-fill: #ffffff;
  }
  html, body {
    margin: 0;
    padding: 0;
    overflow: hidden;
    background: var(--paper);
  }
  .poster {
    position: relative;
    width: 1200px;
    height: 805px;
    overflow: hidden;
    background: var(--paper);
  }
  .brush-strokes {
    position: absolute;
    inset: 0;
  }
  .brush-strokes svg,
  .photo svg {
    display: block;
    width: 100%;
    height: 100%;
  }
  .photo {
    position: absolute;
    left: 120px;
    top: 240px;
    width: 960px;
    height: 565px;
  }
  .brand-line {
    position: absolute;
    right: 60px;
    top: 50px;
    margin: 0;
    font-family: "Cutive Mono", "Courier New", monospace;
    font-size: 70px;
    line-height: 1;
    font-weight: 400;
    color: var(--ink);
    -webkit-text-stroke: 1.5px var(--ink);
    letter-spacing: -2px;
    white-space: nowrap;
    transform: scaleX(0.72);
    transform-origin: right top;
  }
  .title {
    margin: 0;
    font-weight: 400;
  }
  .title span {
    position: absolute;
    font-family: "Special Elite", "Cutive Mono", "Courier New", monospace;
    color: var(--title-teal);
    line-height: 1;
    white-space: nowrap;
    transform-origin: left top;
    text-shadow: 2px 2px 0 var(--title-edge), -1px -1px 0 rgba(255,255,255,0.6);
  }
  .title-the {
    left: 148px;
    top: 236px;
    font-size: 135px;
    transform: scaleX(0.62);
  }
  .title-canvas {
    left: 342px;
    top: 108px;
    font-size: 290px;
    letter-spacing: -6px;
    transform: scaleX(0.64);
  }
  .tagline {
    position: absolute;
    left: 0;
    width: 1160px;
    top: 392px;
    margin: 0;
    text-align: center;
    font-family: "Dancing Script", cursive;
    font-weight: 700;
    font-size: 100px;
    line-height: 1;
    color: var(--tagline-fill);
    white-space: nowrap;
    text-shadow:
      2px 0 0 var(--ink), -2px 0 0 var(--ink),
      0 2px 0 var(--ink), 0 -2px 0 var(--ink),
      2px 2px 0 var(--ink), -2px -2px 0 var(--ink),
      2px -2px 0 var(--ink), -2px 2px 0 var(--ink);
  }
</style>
</head>
<body>
<main class="poster">
  <div class="brush-strokes" role="img" aria-label="Loose watercolour brush strokes in blue, violet, green and pink on white paper">
    <svg viewBox="0 0 1200 805" preserveAspectRatio="none">
      <defs>
        <linearGradient id="wash-top" x1="0" y1="0" x2="1" y2="0.3">
          <stop offset="0" stop-color="var(--stroke-violet)" stop-opacity="0.6"/>
          <stop offset="0.35" stop-color="var(--stroke-blue)" stop-opacity="0.65"/>
          <stop offset="0.7" stop-color="var(--stroke-blue)" stop-opacity="0.4"/>
          <stop offset="1" stop-color="var(--stroke-violet)" stop-opacity="0.5"/>
        </linearGradient>
        <linearGradient id="wash-side" x1="0" y1="0" x2="0" y2="1">
          <stop offset="0" stop-color="var(--stroke-green)" stop-opacity="0.55"/>
          <stop offset="0.5" stop-color="var(--stroke-blue)" stop-opacity="0.4"/>
          <stop offset="1" stop-color="var(--stroke-pink)" stop-opacity="0.55"/>
        </linearGradient>
      </defs>
      <rect width="1200" height="805" fill="var(--paper)"/>
      <path d="M40 60 C200 20 420 40 600 30 C800 20 1000 10 1190 40 L1180 250 C900 230 600 250 300 235 C180 230 80 250 30 240 Z" fill="url(#wash-top)"/>
      <path d="M0 200 C60 190 110 210 140 230 L150 720 C100 730 40 710 0 700 Z" fill="url(#wash-side)"/>
      <path d="M1070 190 C1120 180 1170 200 1200 210 L1200 720 C1150 730 1100 720 1060 700 Z" fill="url(#wash-side)"/>
    </svg>
  </div>

  <div class="photo" role="img" aria-label="Photo of a glowing orange light bulb on a reflective surface, washed from green at the top to red at the bottom">
    <svg viewBox="0 0 960 565" preserveAspectRatio="none">
      <defs>
        <linearGradient id="photo-wash" x1="0" y1="0" x2="0" y2="1">
          <stop offset="0" stop-color="var(--photo-green)"/>
          <stop offset="0.3" stop-color="var(--photo-olive)"/>
          <stop offset="0.55" stop-color="var(--photo-orange)"/>
          <stop offset="1" stop-color="var(--photo-red)"/>
        </linearGradient>
        <linearGradient id="photo-shade" x1="0" y1="0" x2="1" y2="0">
          <stop offset="0" stop-color="var(--photo-dark)" stop-opacity="0.4"/>
          <stop offset="0.45" stop-color="var(--photo-dark)" stop-opacity="0"/>
          <stop offset="1" stop-color="var(--photo-dark)" stop-opacity="0.8"/>
        </linearGradient>
      </defs>
      <rect width="960" height="565" fill="url(#photo-wash)"/>
      <rect width="960" height="565" fill="url(#photo-shade)"/>
    </svg>
  </div>

  <p class="brand-line">Brindle Works products</p>

  <h1 class="title"><span class="title-the">The</span> <span class="title-canvas">Canvas</span></h1>

  <p class="tagline">where I paint my ideas!</p>
</main>
</body>
</html>
```